Property Finance Company - Orbin Funding Limited

Background: Orbin Funding Group Limited is a private property finance company. Orbin Funding Group has capital to directly fund first mortgage, mezzanine and preferred equity financing. We also acquire performing, sub-performing and distressed debt.

Orbin Fundings management philosophy emphasises expertise, innovation, wisdom, honesty and competitiveness. Orbin Funding are not finance brokers - we provide debt funding to the commercial property and residential development sectors. Our process is built from experience and cumutavely Orbin Fundings Directors have in excess of 60 years wisdom.

The aim of the website will be to increase brand awareness, provide clients with comfort around our level of skill and background on who we are, generate more sales, and provide examples of projects that we have funded.

The website is a new product launch, and we need to use our Orbin Funding logo that has just been designed. We like a dark background, and either black/silver/grey/ jade green, or black/gold/jade green colours.

Our unique advantages are that we have fast turnaround times, we can solve clients funding problems and we know what we are doing. Our target audience will be viewing the website on both desktop and mobile devices.

We would like to have the following pages:

Home
About
Team
Services
Project Experience
Contact

Competitors Website: http://www.tarvolo.example/

We would also like to have the option of video footage in our website, as you can see in our competitors website.

Overall we want a really slick, elegant but modern website that is better than www.tarvolo.example

Target Market(s)

Finance borrowers, property developers, accountants, lawyers, businesspeople, high net worth people

Industry/Entity Type

Finance

Requirements
Must have
• Please see project description
Nice to have
Should not have

```html
<!DOCTYPE html>
<html lang="en">
<head>
<meta charset="utf-8">
<title>Orbin Funding Group</title>
<link rel="stylesheet" href="https://fonts.googleapis.com/css2?family=Cinzel:wght@400;700&family=Open+Sans:wght@400;600;700&display=swap">
<style>
:root{
  --jade:#16a05a;
  --jade-dark:#12914f;
  --black:#0e0e0e;
  --ink:#141414;
  --white:#ffffff;
  --muted:#d8d8d8;
  --gray-top:#8c8d8e;
  --gray-mid:#5f6061;
  --gray-low:#4a4b4c;
  --serif:'Cinzel', Georgia, serif;
  --sans:'Open Sans', Arial, sans-serif;
}
*{margin:0;padding:0;box-sizing:border-box}
html,body{width:1200px;height:2946px;overflow:hidden;background:var(--black)}
body{position:relative;font-family:var(--sans);color:var(--white)}
.abs{position:absolute}
section,footer,header{position:absolute;left:0;width:1200px}

/* Hero */
.hero{top:0;height:554px;overflow:hidden}
.hero-photo{position:absolute;inset:0;background:
  radial-gradient(ellipse 520px 260px at 560px 120px,rgba(215,190,120,.55),transparent 70%),
  linear-gradient(180deg,#6d6c55 0%,#4d5a3a 35%,#2f3b26 70%,#1c2318 100%)}
.brand{position:absolute;left:98px;top:62px;width:190px;text-align:center}
.brand-dot{width:58px;height:58px;border-radius:50%;background:var(--white);margin:0 auto 10px}
.brand-name{font-family:var(--serif);font-weight:400;font-size:21px;line-height:1.15;color:var(--white)}
.nav{position:absolute;top:76px;left:414px;display:flex;gap:0;align-items:center}
.nav a{font-family:var(--serif);font-size:16px;color:var(--white);text-decoration:none;margin-right:30px;letter-spacing:.3px}
.nav a.active{color:var(--jade)}
.hero-title{position:absolute;top:222px;width:100%;text-align:center;font-family:var(--serif);font-weight:700;font-size:48px;letter-spacing:1px}
.hero-sub{position:absolute;top:296px;width:100%;text-align:center;font-size:21px;font-weight:600}
.play{position:absolute;left:573px;top:426px}

/* Welcome */
.welcome{top:554px;height:320px;background:var(--ink)}
.welcome-head{position:absolute;left:98px;top:680px;border-left:6px solid var(--jade);padding-left:24px}
.welcome-head .small{font-family:var(--serif);font-size:24px;line-height:1.2}
.welcome-head .big{font-family:var(--serif);font-size:34px;font-weight:700;line-height:1.3}
.welcome-rule{position:absolute;left:448px;top:636px;width:1px;height:160px;background:#333}
.welcome-text{position:absolute;left:524px;top:620px;width:584px;font-size:13.5px;line-height:26.5px;color:var(--muted)}

/* Section titles */
.sec-title{position:absolute;width:100%;text-align:center;font-family:var(--serif);font-size:34px}
.sec-title span{border-left:6px solid var(--white);padding-left:22px}
.sec-title b{font-weight:700}

/* Services */
.services{top:874px;height:452px;background:linear-gradient(180deg,var(--gray-mid),#6c6d6e 50%,var(--gray-low))}
.service-name{position:absolute;font-family:var(--serif);font-size:21px;line-height:30px}
.service-text{position:absolute;font-size:14px;line-height:23px;color:#eee;width:290px}
.btn-outline{position:absolute;border:1px solid var(--white);font-size:12.5px;font-weight:700;padding:0 14px;height:34px;line-height:32px;letter-spacing:.3px}

/* Why */
.why{top:1326px;height:436px;background:var(--jade)}
.why-item{position:absolute;top:1481px;width:200px;text-align:center}
.why-circle{width:156px;height:156px;border:2px solid var(--white);border-radius:50%;margin:0 auto;display:flex;align-items:center;justify-content:center}
.why-label{margin-top:26px;font-size:21px;font-weight:600}

/* Projects */
.projects{top:1762px;height:628px;background:linear-gradient(180deg,var(--gray-top),#6f7071 60%,#5a5b5c)}
.project{position:absolute;overflow:hidden}
.project .photo{position:absolute;inset:0}
.project .caption{position:absolute;left:0;right:0;bottom:0;height:43px;background:rgba(20,20,20,.78);text-align:center;font-size:18px;line-height:43px}

/* Footer */
.footer{top:2390px;height:556px;background:linear-gradient(180deg,#111,#1b1f1c 50%,#101210)}
.to-top{position:absolute;left:560px;top:2428px;width:80px;text-align:center;font-size:12.5px;font-weight:700}
.foot-head{position:absolute;top:2538px;font-family:var(--serif);font-size:24px;font-weight:700}
.field{position:absolute;background:var(--white);color:#777;font-size:11px;padding:0 12px;line-height:32px}
.submit{position:absolute;left:632px;top:2797px;width:95px;height:35px;background:var(--jade);font-size:14px;font-weight:700;text-align:center;line-height:35px}
.info{position:absolute;left:780px;display:flex;align-items:center;font-size:12px}
.info .ic{width:34px;height:34px;border:1px solid #666;border-radius:50%;display:flex;align-items:center;justify-content:center;margin-right:24px}
.social{position:absolute;top:2770px;width:34px;height:34px;border-radius:50%}
.foot-rule{position:absolute;left:98px;top:2867px;width:1004px;height:1px;background:#2e2e2e}
.copyright{position:absolute;top:2898px;width:100%;text-align:center;font-size:12px;color:#ccc}
</style>
</head>
<body>

<header class="hero">
  <div class="hero-photo" role="img" aria-label="Aerial view of farmland and a country road at sunrise"></div>
  <div class="brand"><div class="brand-dot"></div><div class="brand-name">Orbin Funding<br>Group</div></div>
  <nav class="nav">
    <a class="active">Home</a><a>About</a><a>Team</a><a>Services</a><a>Project Experience</a><a>Contact</a>
    <svg width="18" height="18" viewBox="0 0 18 18"><circle cx="7" cy="7" r="5.5" fill="none" stroke="#fff" stroke-width="2.4"/><line x1="11" y1="11" x2="16" y2="16" stroke="#fff" stroke-width="2.6"/></svg>
  </nav>
  <h1 class="hero-title">ORBIN FUNDING GROUP</h1>
  <p class="hero-sub">Orbin Funding Group Limited is a private property finance company</p>
  <svg class="play" width="56" height="56" viewBox="0 0 56 56"><circle cx="28" cy="28" r="26" fill="rgba(0,0,0,.25)" stroke="#fff" stroke-width="2.5"/><path d="M22 17 L39 28 L22 39Z" fill="#fff"/></svg>
</header>

<section class="welcome"></section>
<div class="welcome-head"><div class="small">WELCOME TO</div><div class="big">ORBIN FUNDING</div></div>
<div class="welcome-rule"></div>
<p class="welcome-text">Orbin Funding Group Limited is a private property finance company. Orbin Funding Group has capital to directly fund first mortgage, mezzanine and preferred equity financing. We also acquire performing, sub-performing and distressed debt. Orbin Fundings management philosophy emphasises expertise, innovation, wisdom, honesty and competitiveness. Orbin Funding are not finance brokers - we provide debt funding to the commercial property and residential development sectors. Our process is built from experience and cumutavely Orbin Fundings Directors have in excess of 60 years wisdom.</p>

<section class="services"></section>
<h2 class="sec-title" style="top:940px"><span>OUR <b>SERVICES</b></span></h2>
<svg class="abs" style="left:122px;top:1037px" width="118" height="152" viewBox="0 0 118 152" fill="none" stroke="#fff" stroke-width="7">
  <path d="M4 24 L28 4 H114 V148 H4 Z"/><path d="M28 4 V24 H4"/>
  <path d="M48 56 L70 38 L92 56 M54 52 V72 H86 V52" stroke-width="6"/>
  <path d="M40 100 c-10 0-10 12 0 12 c10 0 10 12 0 12 M40 92 V132" stroke-width="6"/>
  <line x1="60" y1="104" x2="100" y2="104"/><line x1="60" y1="118" x2="100" y2="118"/><line x1="60" y1="132" x2="100" y2="132"/>
</svg>
<div class="service-name" style="left:283px;top:1043px">DIRECT FUND<br>FIRST MORTGAGE</div>
<p class="service-text" style="left:283px;top:1117px">Our process is built from experience and cumutavely Orbin Fundings Directors have in excess of 60 years wisdom.</p>
<div class="btn-outline" style="left:283px;top:1214px">READ MORE</div>

<svg class="abs" style="left:620px;top:1045px" width="172" height="130" viewBox="0 0 172 130" fill="none" stroke="#fff" stroke-width="6">
  <rect x="4" y="30" width="110" height="66"/><rect x="16" y="42" width="110" height="66"/>
  <rect x="28" y="54" width="130" height="72" fill="#fff"/>
  <circle cx="93" cy="90" r="20" fill="#5f6061" stroke="none"/>
  <text x="93" y="100" text-anchor="middle" font-family="Open Sans,sans-serif" font-weight="700" font-size="28" fill="#fff" stroke="none">$</text>
  <circle cx="140" cy="28" r="26" fill="#fff" stroke="none"/>
  <path d="M126 22 H154 M146 14 L154 22 L146 30 M154 36 H126 M134 28 L126 36 L134 44" stroke="#5f6061" stroke-width="4"/>
</svg>
<div class="service-name" style="left:819px;top:1043px">MEZZANINE &amp; PREFERRED<br>EQUITY FINANCING</div>
<p class="service-text" style="left:819px;top:1117px">Our process is built from experience and cumutavely Orbin Fundings Directors have in excess of 60 years wisdom.</p>
<div class="btn-outline" style="left:819px;top:1214px">READ MORE</div>

<section class="why"></section>
<h2 class="sec-title" style="top:1394px"><span>WHY <b>CHOOSE US</b></span></h2>
<div class="why-item" style="left:77px"><div class="why-circle"><svg width="64" height="70" viewBox="0 0 64 70" fill="#fff"><circle cx="32" cy="18" r="16"/><path d="M2 68 C2 44 14 38 32 38 C50 38 62 44 62 68Z"/></svg></div><div class="why-label">Expertise</div></div>
<div class="why-item" style="left:289px"><div class="why-circle"><svg width="50" height="70" viewBox="0 0 50 70" fill="none" stroke="#fff" stroke-width="5"><path d="M15 46 C15 38 4 32 4 20 A21 21 0 0 1 46 20 C46 32 35 38 35 46Z"/><line x1="16" y1="54" x2="34" y2="54"/><line x1="18" y1="62" x2="32" y2="62"/></svg></div><div class="why-label">Innovation</div></div>
<div class="why-item" style="left:499px"><div class="why-circle"><svg width="72" height="66" viewBox="0 0 72 66" fill="#fff"><path d="M16 2 H70 L58 52 H4Z"/><path d="M4 52 H58 L56 62 H2Z" fill="none" stroke="#fff" stroke-width="4"/><path d="M24 14 H58 M22 24 H56" stroke="#16a05a" stroke-width="4"/></svg></div><div class="why-label">Wisdom</div></div>
<div class="why-item" style="left:711px"><div class="why-circle"><svg width="74" height="66" viewBox="0 0 74 66" fill="#fff"><rect x="2" y="28" width="16" height="36"/><path d="M24 30 L38 6 C44 2 48 8 46 14 L42 26 H66 C72 26 74 34 68 36 C74 38 72 46 66 46 C70 50 66 56 62 56 C64 60 60 64 56 64 H24Z"/></svg></div><div class="why-label">Honesty</div></div>
<div class="why-item" style="left:921px"><div class="why-circle"><svg width="80" height="60" viewBox="0 0 80 60"><path d="M8 56 V40 L24 14 L38 34 L52 22 L72 44 V56Z" fill="#fff"/><path d="M4 2 V58 H78" fill="none" stroke="#fff" stroke-width="5"/></svg></div><div class="why-label">Competitiveness</div></div>

<section class="projects"></section>
<h2 class="sec-title" style="top:1828px"><span>OUR <b>PROJECTS</b></span></h2>
<div class="project" style="left:98px;top:1919px;width:452px;height:397px"><div class="photo" role="img" aria-label="Modern glass apartment building at dusk" style="background:linear-gradient(160deg,#3f6f9a,#2b3b48 45%,#7a5a3a 75%,#2a2a2a)"></div><div class="caption">Finibus Bonorum et Malorum</div></div>
<div class="project" style="left:568px;top:1919px;width:257px;height:188px"><div class="photo" role="img" aria-label="Apartment block against a blue sky" style="background:linear-gradient(150deg,#8fb3d4,#b59a6e 55%,#4a4030)"></div><div class="caption">Finibus Bon Malor</div></div>
<div class="project" style="left:843px;top:1919px;width:257px;height:188px"><div class="photo" role="img" aria-label="Aerial view of a suburban housing estate" style="background:linear-gradient(150deg,#7a8a5a,#a0765a 50%,#4d5a3c)"></div><div class="caption">Finibus Bon Malor</div></div>
<div class="project" style="left:568px;top:2127px;width:257px;height:189px"><div class="photo" role="img" aria-label="Two storey family house with garden" style="background:linear-gradient(180deg,#6f9fd0,#7a8aa0 45%,#4f6e3a)"></div><div class="caption">Finibus Bon Malor</div></div>
<div class="project" style="left:843px;top:2127px;width:257px;height:189px"><div class="photo" role="img" aria-label="Street between modern apartment buildings" style="background:linear-gradient(180deg,#5ea0e0,#8a7a5a 50%,#3a3a3a)"></div><div class="caption">Finibus Bon Malor</div></div>

<footer class="footer"></footer>
<div class="to-top"><svg width="70" height="22" viewBox="0 0 70 22"><path d="M0 22 L35 0 L70 22Z" fill="#bdbdbd"/></svg><div>TO TOP</div></div>
<div class="foot-head" style="left:98px">CONTACT FORM</div>
<div class="foot-head" style="left:780px">CONTACT INFORMATION</div>
<div class="field" style="left:98px;top:2608px;width:310px;height:32px">Name :</div>
<div class="field" style="left:417px;top:2608px;width:310px;height:32px">Phone no :</div>
<div class="field" style="left:98px;top:2653px;width:629px;height:32px">Email :</div>
<div class="field" style="left:98px;top:2699px;width:629px;height:80px">Message :</div>
<div class="submit">SUBMIT</div>

<div class="info" style="top:2595px"><span class="ic"><svg width="14" height="18" viewBox="0 0 14 18"><path d="M7 1 A6 6 0 0 1 13 7 C13 11 7 17 7 17 C7 17 1 11 1 7 A6 6 0 0 1 7 1Z" fill="#fff"/><circle cx="7" cy="7" r="2.2" fill="#111"/></svg></span>27 Marlow Terrace, Eastvale Harbour</div>
<div class="info" style="top:2654px"><span class="ic"><svg width="16" height="16" viewBox="0 0 16 16"><path d="M3 1 L6 4 L4.5 6.5 C5.5 8.5 7.5 10.5 9.5 11.5 L12 10 L15 13 L13 15 C7 15 1 9 1 3Z" fill="#fff"/></svg></span>0 800 555 0142</div>
<div class="info" style="top:2709px"><span class="ic"><svg width="16" height="12" viewBox="0 0 16 12"><rect x="0" y="0" width="16" height="12" rx="1" fill="#fff"/><path d="M1 1 L8 7 L15 1" fill="none" stroke="#111" stroke-width="1.5"/></svg></span>info@orbinfunding.example</div>
<div class="social" style="left:780px;background:#2f5fa8"></div>
<div class="social" style="left:824px;background:#2a9fd8"></div>
<div class="social" style="left:867px;background:#1d6fa8"></div>
<div class="social" style="left:910px;background:#c8232c"></div>
<div class="foot-rule"></div>
<p class="copyright">Copyright © 2017, Orbin Funding. All rights reserved.</p>

</body>
</html>
```